Clean business card with logo provided

I want a card that will stand out among the masses. I need the color and image to show professionalism and yet have a family appeal showing that I only deal with win/win scenarios. The back of the card will be used to take notes about the individual so I can use that in my database entry. I like modern design but need professionalism in it also. It needs to fit my "clean, safe, and affordable housing" motto. I need to be able to write on the file and update the card details for my employees.

Target Market(s)

Investors looking to make investment income through real estate

Industry/Entity Type

Real Estate

Contact Information for Business Card

Brent Kovalich
blank address, city, st, zip code
480-555-3174
brentkovalich@ridgeworthrentals.example
www.ridgeworthrentals.example

Font styles to use
Sans Serif

Requirements
Must have
• I would like the back of the card to have lines for info. example
• Met/Visited: Date:
• Interets:
Nice to have
• I want the cards color to match the logo background color. Font with details to be san serif and black. I want the card rectangular with square corners. Standard business card size. I would like to see cards designed with both images to see which i prefer more.

```html
<!DOCTYPE html>
<html lang="en">
<head>
<meta charset="utf-8">
<title>Ridgeworth Rentals – Business Card</title>
<link rel="stylesheet" href="https://fonts.googleapis.com/css2?family=Open+Sans:wght@400;600;700&display=swap">
<style>
  :root {
    --teal: #00b5cc;
    --ink: #111111;
    --white: #ffffff;
    --canvas: #e9e6e3;
    --dots: #222222;
  }
  * { margin: 0; padding: 0; box-sizing: border-box; }
  html, body { width: 1200px; height: 900px; overflow: hidden; }
  body {
    background: var(--canvas);
    font-family: "Open Sans", Arial, sans-serif;
    position: relative;
  }
  .card {
    position: absolute;
    background: var(--white);
    overflow: hidden;
    box-shadow: 0 6px 18px rgba(0,0,0,.18);
  }
  .card-bands { position: absolute; inset: 0; width: 100%; height: 100%; }
  .card--front { left: 77px; top: 33px; width: 589px; height: 364px; }
  .card--back { left: 388px; top: 505px; width: 567px; height: 352px; }

  .wordmark {
    position: absolute;
    font-weight: 600;
    white-space: nowrap;
    text-align: center;
  }
  .card--front .wordmark {
    left: 40px; width: 510px; top: 82px;
    font-size: 24px; letter-spacing: 2px; color: var(--teal);
  }
  .card--back .wordmark {
    left: 40px; width: 487px; top: 236px;
    font-size: 22px; letter-spacing: 1.5px; color: var(--white);
  }

  .tagline { position: absolute; font-weight: 600; white-space: nowrap; }
  .card--front .tagline { left: 107px; top: 150px; font-size: 13px; color: var(--teal); }
  .card--back .tagline { left: 120px; top: 317px; font-size: 11.5px; color: var(--white); }

  .contact-list {
    position: absolute; right: 281px; top: 250px;
    list-style: none; text-align: right; color: var(--white);
    font-size: 13px; line-height: 25px;
  }
  .contact-list li { display: flex; align-items: center; justify-content: flex-end; gap: 6px; white-space: nowrap; }
  .contact-list svg { width: 11px; height: 11px; fill: var(--white); flex: none; }

  .holder { position: absolute; left: 342px; top: 242px; color: var(--white); }
  .holder-name { font-size: 20px; font-weight: 600; margin-bottom: 14px; }
  .holder-address { font-size: 15px; line-height: 19px; }

  .notes { position: absolute; left: 107px; top: 40px; width: 355px; }
  .note-row { display: flex; align-items: baseline; height: 40px; }
  .note-label { color: var(--teal); font-weight: 600; font-size: 16px; white-space: nowrap; margin-right: 6px; }
  .note-line { flex: 1; border-bottom: 2px dotted var(--dots); transform: translateY(-4px); }
  .note-row:first-child .note-label { margin-right: 20px; }
</style>
</head>
<body>

<section class="card card--front" aria-label="Business card front">
  <svg class="card-bands" viewBox="0 0 589 364" preserveAspectRatio="none" aria-hidden="true">
    <polygon points="0,189 400,189 382,214 0,214" fill="var(--ink)"/>
    <polygon points="0,218 386,218 414,181 589,181 589,364 0,364" fill="var(--teal)"/>
  </svg>
  <div class="wordmark">RIDGEWORTH RENTALS LLC</div>
  <p class="tagline">Providing clean, safe, and affordable housing</p>

  <ul class="contact-list">
    <li>480-555-3174
      <svg viewBox="0 0 24 24"><path d="M6.6 10.8a15 15 0 0 0 6.6 6.6l2.2-2.2a1 1 0 0 1 1-.25 11.4 11.4 0 0 0 3.6.57 1 1 0 0 1 1 1V20a1 1 0 0 1-1 1A17 17 0 0 1 3 4a1 1 0 0 1 1-1h3.5a1 1 0 0 1 1 1c0 1.25.2 2.45.57 3.57a1 1 0 0 1-.25 1z"/></svg></li>
    <li>brentkovalich@ridgeworthrentals.example
      <svg viewBox="0 0 24 24"><path d="M2 5h20v14H2z M4 7v.5l8 5 8-5V7z" fill-rule="evenodd"/></svg></li>
    <li>www.ridgeworthrentals.example
      <svg viewBox="0 0 24 24"><circle cx="12" cy="12" r="10"/><path d="M12 2v20M2 12h20" stroke="var(--teal)" stroke-width="1.6" fill="none"/></svg></li>
  </ul>

  <div class="holder">
    <p class="holder-name">Brent Kovalich</p>
    <p class="holder-address">12345, Address Goes Here<br>Country Name, 123456</p>
  </div>
</section>

<section class="card card--back" aria-label="Business card back">
  <svg class="card-bands" viewBox="0 0 567 352" preserveAspectRatio="none" aria-hidden="true">
    <polygon points="0,168 362,168 343,194 0,194" fill="var(--ink)"/>
    <polygon points="0,197 348,197 376,160 567,160 567,352 0,352" fill="var(--teal)"/>
  </svg>
  <div class="notes">
    <div class="note-row"><span class="note-label">Visited Date:</span><span class="note-line"></span></div>
    <div class="note-row"><span class="note-label">Interets:</span><span class="note-line"></span></div>
    <div class="note-row"><span class="note-label">Problems:</span><span class="note-line"></span></div>
  </div>
  <div class="wordmark">RIDGEWORTH RENTALS LLC</div>
  <p class="tagline">Providing clean, safe, and affordable housing</p>
</section>

</body>
</html>
```